TALMORK

The business want a professional looking business card. We have a scetch we will add but want the extra upgrade, and would like more suggestions for variations of our business cards.

```html
<!DOCTYPE html>
<html lang="en">
<head>
<meta charset="utf-8">
<title>TALMORK – Business Card</title>
<link rel="stylesheet" href="https://fonts.googleapis.com/css2?family=Montserrat:wght@400;600;700&display=swap">
<style>
  :root {
    --backdrop: #141414;
    --card: #1e1e1e;
    --card-edge: #252525;
    --gold: #c9a24a;
    --ink-light: #f2f2f2;
  }
  * { margin: 0; padding: 0; box-sizing: border-box; }
  html, body {
    width: 1200px; height: 1059px; overflow: hidden;
    background: var(--backdrop);
    font-family: "Montserrat", Arial, sans-serif;
  }
  .canvas { position: relative; width: 1200px; height: 1059px; }

  .card {
    position: absolute;
    border-radius: 20px;
    background: linear-gradient(160deg, var(--card-edge), var(--card) 55%);
    overflow: hidden;
  }
  .card--front { left: 257px; top: 89px; width: 687px; height: 390px; }
  .card--back  { left: 254px; top: 547px; width: 693px; height: 393px; }

  .brand { position: absolute; text-align: center; color: var(--gold); }
  .brand__dot { display: block; margin: 0 auto; border-radius: 50%; background: var(--gold); }
  .brand__name { display: block; font-weight: 600; color: var(--gold); }

  .card--front .brand { left: 33px; top: 52px; width: 180px; }
  .card--front .brand__dot { width: 62px; height: 62px; }
  .card--front .brand__name { margin-top: 26px; font-size: 24px; letter-spacing: 6px; }

  .card--back .brand { left: 0; top: 118px; width: 100%; }
  .card--back .brand__dot { width: 110px; height: 110px; }
  .card--back .brand__name { margin-top: 38px; font-size: 42px; letter-spacing: 10px; }

  .person { position: absolute; right: 37px; top: 60px; text-align: right; }
  .person__name { font-size: 23px; font-weight: 700; color: var(--gold); line-height: 1.2; }
  .person__role { font-size: 18px; font-weight: 400; color: var(--ink-light); line-height: 1.3; }

  .contact { position: absolute; left: 37px; top: 256px; list-style: none; }
  .contact__item {
    display: flex; align-items: center; gap: 10px;
    height: 34px; font-size: 19px; color: var(--ink-light);
  }
  .contact__icon { width: 15px; height: 15px; fill: var(--gold); flex: none; }

  .card__accent {
    position: absolute; right: -60px; bottom: -90px;
    width: 260px; height: 260px; border-radius: 50%;
    background: radial-gradient(circle at 40% 35%, #3a3a3a, #262626 70%);
    opacity: 0.7;
  }
</style>
</head>
<body>
<main class="canvas">

  <section class="card card--front">
    <div class="brand">
      <span class="brand__dot"></span>
      <span class="brand__name">TALMORK</span>
    </div>

    <div class="person">
      <p class="person__name">Aksel Brenne Holt</p>
      <p class="person__role">CEO &amp; Founder</p>
    </div>

    <ul class="contact">
      <li class="contact__item">
        <svg class="contact__icon" viewBox="0 0 24 24" aria-hidden="true"><path d="M6.6 10.8a15.1 15.1 0 0 0 6.6 6.6l2.2-2.2a1 1 0 0 1 1-.25 11.4 11.4 0 0 0 3.6.57 1 1 0 0 1 1 1V20a1 1 0 0 1-1 1A17 17 0 0 1 3 4a1 1 0 0 1 1-1h3.5a1 1 0 0 1 1 1c0 1.25.2 2.45.57 3.57a1 1 0 0 1-.25 1z"/></svg>
        <span>004791436025</span>
      </li>
      <li class="contact__item">
        <svg class="contact__icon" viewBox="0 0 24 24" aria-hidden="true"><path d="M2 9l10-7 10 7v12H2zm2 1.2V19h16v-8.8l-8 5.6z"/></svg>
        <span>talmork.llc@mailbox.com</span>
      </li>
      <li class="contact__item">
        <svg class="contact__icon" viewBox="0 0 24 24" aria-hidden="true"><path d="M12 2a10 10 0 1 0 0 20 10 10 0 0 0 0-20zm-1 17.9A8 8 0 0 1 4.1 11H8c0 3 1 6.2 3 8.9zM8 9H4.3A8 8 0 0 1 11 4.1C9.3 5.6 8.3 7.2 8 9zm5 10.9c2-2.7 3-5.9 3-8.9h3.9a8 8 0 0 1-6.9 8.9zM16 9c-.3-1.8-1.3-3.4-3-4.9A8 8 0 0 1 19.7 9z"/></svg>
        <span>www.talmork.llc</span>
      </li>
    </ul>

    <div class="card__accent" aria-hidden="true"></div>
  </section>

  <section class="card card--back">
    <div class="brand">
      <span class="brand__dot"></span>
      <span class="brand__name">TALMORK</span>
    </div>
  </section>

</main>
</body>
</html>
```